Create a Stalvik-looking dashboard for our Open Compass Speedometer that can look similar to my AI-generated dashboard attached, but with: 1) clear borders on all four sides, 2) is created in a way that we can modify the numbers weekly, say maybe you create the graphic that we can inset the excel spreadsheet numbers into, but ideally mixed with the Stalvik look black leather bubble design shown in the dashboard?; 3) uses the exact numbers shown in the attachment; 4) the speedometer on top should have four equal colors of red on left (-1), then yellow (0), then light green (1), then medium green (2); 5) the gauge on the top left should be the graphic that includes 0-100% bar that is currently 33%, and right below that a -20 to +20 bar with the arrow pointing to 11.9%, with color coding similar to the graphic; 6) replace the Stalvik logo in the middle with a similar shaped shield with blue background with the "T" logo with the eagle inside it, like attached

```html
<!DOCTYPE html>
<html lang="en">
<head>
<meta charset="utf-8">
<title>Open Compass Speedometer</title>
<link href="https://fonts.googleapis.com/css2?family=Barlow+Semi+Condensed:ital,wght@0,500;0,600;0,700;1,700&family=Barlow:wght@400;500&display=swap" rel="stylesheet">
<style>
:root{
  --bg-1:#343434;
  --bg-2:#1e1e1e;
  --shell:#0b0b0b;
  --shell-edge:#8a8a8a;
  --leather-1:#d0242c;
  --leather-2:#7d0d12;
  --gold:#e9b94a;
  --gold-light:#f6dc93;
  --cream:#f3e1b0;
  --label:#e3e3e3;
  --muted:#9a9a9a;
  --ink:#101010;
  --g2a:#2ccb3e; --g2b:#0c8a1c;
  --g1a:#a9e02c; --g1b:#73ad0c;
  --g0a:#d4c413; --g0b:#9f8f04;
  --gra:#e2382c; --grb:#a91810;
  --total-yellow:#ffd21e;
}
*{box-sizing:border-box;margin:0;padding:0}
html,body{width:1200px;height:1200px;overflow:hidden}
body{
  position:relative;
  background:
    repeating-linear-gradient(45deg,rgba(255,255,255,.025) 0 2px,rgba(0,0,0,.06) 2px 4px),
    radial-gradient(ellipse at 50% 40%,var(--bg-1),var(--bg-2));
  font-family:"Barlow Semi Condensed",sans-serif;
  color:var(--label);
}
.shell{position:absolute;left:0;top:0;width:1200px;height:1200px}
.title{
  position:absolute;left:0;width:1200px;top:366px;text-align:center;
  font-size:23px;font-weight:700;color:var(--gold);letter-spacing:.3px;
  text-shadow:0 1px 0 #5a3d08;
}
.title em{font-style:italic}
.title sup{font-size:10px;vertical-align:11px}

/* Gear status table */
.status-head{position:absolute;top:416px;font-size:15px;font-weight:700;color:var(--label);transform:translateX(-50%);letter-spacing:.3px}
.status-row{position:absolute;display:flex;height:34px;font-size:14px;font-weight:700;color:var(--ink);border-top:2px solid rgba(255,230,80,.55)}
.status-row>div{display:flex;align-items:center;height:100%;border-right:2px solid #111}
.status-row>div:last-child{border-right:0}
.status-row .c-trend{justify-content:center;width:161px}
.status-row .c-date{padding-left:20px;flex:1}
.row-bull{left:267px;width:652px;top:447px;background:linear-gradient(var(--g2a),var(--g2b))}
.row-bull .c-gear{width:261px;padding-left:56px}
.row-bullish,.row-bearish,.row-bear{left:291px;width:606px}
.row-bullish .c-gear,.row-bearish .c-gear,.row-bear .c-gear{width:237px;padding-left:32px}
.row-bullish{top:483px;background:linear-gradient(var(--g1a),var(--g1b))}
.row-bearish{top:519px;background:linear-gradient(var(--g0a),var(--g0b))}
.row-bear{top:555px;background:linear-gradient(var(--gra),var(--grb))}

/* Trend summary table */
.summary-head{position:absolute;left:291px;top:602px;width:603px;height:38px;background:#121212}
.summary-head span{position:absolute;top:50%;transform:translate(-50%,-50%);font-size:11px;font-weight:700;line-height:1.1;text-align:center;color:var(--label)}
.summary-head span.left{transform:translateY(-50%)}
.summary-row{position:absolute;left:293px;width:601px;height:28px;font-size:13px;font-weight:600;color:var(--ink)}
.summary-row span{position:absolute;top:50%;transform:translate(-50%,-50%);white-space:nowrap}
.summary-row span.name{left:19px;transform:translateY(-50%)}
.s-turbo{top:652px;background:linear-gradient(var(--g2a),var(--g2b))}
.s-accel{top:681px;background:linear-gradient(var(--g1a),var(--g1b))}
.s-brakes{top:710px;background:linear-gradient(var(--g0a),var(--g0b))}
.s-reverse{top:739px;background:linear-gradient(var(--gra),var(--grb))}
.total-row{position:absolute;left:293px;top:774px;width:601px;height:22px;background:linear-gradient(90deg,transparent,#151515 20%,#151515 80%,transparent)}
.total-row span{position:absolute;top:50%;transform:translateY(-50%);white-space:nowrap}
.total-label{left:118px;font-size:14px;font-weight:700;color:var(--label)}
.total-days{left:185px;font-size:12px;font-weight:700;color:var(--total-yellow)}
.total-note{left:235px;font-family:"Barlow",sans-serif;font-size:10.5px;color:#cfcfcf}

.rule{position:absolute;left:305px;width:578px;height:2px;background:linear-gradient(90deg,transparent,#bdbdbd 15%,#bdbdbd 85%,transparent)}

/* Trend logic grid */
.logic-title{position:absolute;left:0;width:1192px;top:813px;text-align:center;font-size:14px;font-weight:700;color:var(--cream);letter-spacing:.2px}
.cell{position:absolute;display:flex;align-items:center;justify-content:center;text-align:center;font-weight:600;color:var(--ink);line-height:1}
.cell.h{font-size:10.5px;height:26px}
.cell.l{font-size:8.5px;height:28px;justify-content:flex-end;padding-right:6px}
.cell.v{font-size:8.5px;height:28px}
.tg{background:linear-gradient(var(--g2a),var(--g2b))}
.tl{background:linear-gradient(var(--g1a),var(--g1b))}
.ty{background:linear-gradient(var(--g0a),var(--g0b))}
.tr{background:linear-gradient(var(--gra),var(--grb))}
.cell.pos{background:linear-gradient(var(--g2a),var(--g2b))}
.cell.neg{background:linear-gradient(var(--gra),var(--grb))}

.disclaimer{
  position:absolute;left:310px;width:572px;top:995px;text-align:center;
  font-family:"Barlow",sans-serif;font-size:8.6px;line-height:12.4px;color:var(--muted);
}
</style>
</head>
<body>

<svg class="shell" viewBox="0 0 1200 1200" aria-hidden="true">
  <defs>
    <linearGradient id="leather" x1="0" y1="0" x2="0" y2="1">
      <stop offset="0" stop-color="var(--leather-1)"/>
      <stop offset="1" stop-color="var(--leather-2)"/>
    </linearGradient>
    <linearGradient id="bezel" x1="0" y1="0" x2="0" y2="1">
      <stop offset="0" stop-color="#9a9a9a"/>
      <stop offset=".5" stop-color="#2a2a2a"/>
      <stop offset="1" stop-color="#707070"/>
    </linearGradient>
    <linearGradient id="ryg" x1="0" y1="0" x2="1" y2="0">
      <stop offset="0" stop-color="#c81e14"/>
      <stop offset=".5" stop-color="#c9a416"/>
      <stop offset="1" stop-color="#17902a"/>
    </linearGradient>
    <radialGradient id="hubGold" cx=".35" cy=".35" r=".7">
      <stop offset="0" stop-color="#ffe7a0"/>
      <stop offset="1" stop-color="#b9781a"/>
    </radialGradient>
    <linearGradient id="needleGold" x1="0" y1="0" x2="1" y2="0">
      <stop offset="0" stop-color="#c58b22"/>
      <stop offset="1" stop-color="#ffe08a"/>
    </linearGradient>
  </defs>

  <!-- gauge cluster housing -->
  <path d="M158,420 L158,330 C158,270 200,240 260,228 L420,205 C470,160 540,145 604,145 C668,145 738,160 788,205 L948,228 C1008,240 1030,270 1030,330 L1030,420 Z" fill="var(--shell)" stroke="#5c5c5c" stroke-width="3"/>

  <!-- leather hood -->
  <path d="M162,290 C160,235 200,205 270,190 L410,168 C460,135 535,120 604,120 C673,120 748,135 798,168 L938,190 C1008,205 1025,235 1020,290 L1000,285 C995,250 970,235 930,228 L790,210 C740,165 670,150 604,150 C538,150 468,165 418,210 L278,228 C238,235 190,250 185,285 Z" fill="url(#leather)"/>
  <path d="M175,270 C180,232 215,212 272,200 L414,178 C464,146 537,132 604,132 C671,132 744,146 794,178 L936,200 C993,212 1008,232 1010,270" fill="none" stroke="#f06a6a" stroke-opacity=".35" stroke-width="1" stroke-dasharray="3 3"/>

  <!-- central gauge -->
  <circle cx="604" cy="333" r="196" fill="#050505" stroke="url(#bezel)" stroke-width="6"/>
  <circle cx="604" cy="333" r="176" fill="#0a0a0a" stroke="#3a3a3a" stroke-width="2"/>
  <path d="M604,333 L449,333 A155,155 0 0 1 494.4,223.4 Z" fill="#c4201a"/>
  <path d="M604,333 L494.4,223.4 A155,155 0 0 1 604,178 Z" fill="#cdb315"/>
  <path d="M604,333 L604,178 A155,155 0 0 1 713.6,223.4 Z" fill="#8fd02a"/>
  <path d="M604,333 L713.6,223.4 A155,155 0 0 1 759,333 Z" fill="#1f9e33"/>
  <path d="M439,333 A165,165 0 0 1 769,333" fill="none" stroke="#8c8c8c" stroke-width="8" stroke-dasharray="1.4 3.2"/>
  <g font-family="Barlow Semi Condensed, sans-serif" font-weight="700" font-size="24" text-anchor="middle">
    <text x="470" y="315" fill="#f2f2f2">-1</text>
    <text x="533" y="242" fill="#f2c24a">0</text>
    <text x="666" y="242" fill="#f2e27a">1</text>
    <text x="726" y="315" fill="#f2c24a">2</text>
  </g>
  <circle cx="604" cy="248" r="4" fill="var(--gold)"/>
  <text x="614" y="252" font-family="Barlow Semi Condensed, sans-serif" font-weight="700" font-size="11" fill="var(--gold)">OPEN COMPASS</text>
  <path d="M544,336 A60,60 0 0 1 664,336 Z" fill="#101010" stroke="#4a4a4a" stroke-width="3"/>
  <polygon points="600,336 608,330 688,238" fill="url(#needleGold)"/>
  <circle cx="604" cy="333" r="14" fill="url(#hubGold)"/>

  <!-- earnings-beat sub gauge -->
  <circle cx="357" cy="262" r="46" fill="#080808" stroke="url(#bezel)" stroke-width="4"/>
  <path id="beatArc" d="M322,262 A35,35 0 0 1 392,262" fill="none"/>
  <text font-family="Barlow Semi Condensed, sans-serif" font-weight="700" font-size="5.6" fill="#f0d27a"><textPath href="#beatArc" startOffset="4">COMPANIES BEATING EARNINGS ESTIMATES</textPath></text>
  <text x="358" y="268" text-anchor="middle" font-family="Barlow Semi Condensed, sans-serif" font-weight="700" font-size="12" fill="#f4f4f4">75%</text>

  <!-- reporting gauge -->
  <circle cx="309" cy="359" r="92" fill="#050505" stroke="url(#bezel)" stroke-width="5"/>
  <path d="M253.6,391 A64,64 0 1 1 372.8,354.5" fill="none" stroke="url(#ryg)" stroke-width="32"/>
  <path d="M244,396.5 A75,75 0 1 1 383.8,353.8" fill="none" stroke="#888" stroke-width="5" stroke-dasharray="1 2.6"/>
  <g font-family="Barlow Semi Condensed, sans-serif" font-weight="700" font-size="8" fill="#f4f4f4" text-anchor="middle">
    <text x="261" y="390">0%</text>
    <text x="250" y="345">25%</text>
    <text x="293" y="304">50%</text>
    <text x="348" y="316">75%</text>
    <text x="368" y="358">100%</text>
  </g>
  <polygon points="273.5,331.3 251.8,314.4 275.8,328.4" fill="#f4f4f4"/>
  <circle cx="309" cy="359" r="43" fill="#0d0d0d" stroke="#5a5a5a" stroke-width="3"/>
  <g font-family="Barlow Semi Condensed, sans-serif" text-anchor="middle">
    <text x="309" y="343" font-size="6.4" font-weight="600" fill="#9fc7e8">COMPANIES</text>
    <text x="309" y="349" font-size="6.4" font-weight="600" fill="#9fc7e8">REPORTING QTD</text>
    <text x="310" y="368" font-size="18" font-weight="700" fill="#f4f4f4">33%</text>
    <text x="309" y="380" font-size="6.4" font-weight="600" fill="#cfcfcf">(165/500)</text>
  </g>

  <!-- EPS growth gauge -->
  <circle cx="885" cy="360" r="92" fill="#050505" stroke="url(#bezel)" stroke-width="5"/>
  <path d="M822,348.9 A64,64 0 1 1 942,389" fill="none" stroke="url(#ryg)" stroke-width="32"/>
  <path d="M811.1,347 A75,75 0 1 1 951.8,394" fill="none" stroke="#888" stroke-width="5" stroke-dasharray="1 2.6"/>
  <g font-family="Barlow Semi Condensed, sans-serif" font-weight="700" font-size="8" fill="#f4f4f4" text-anchor="middle">
    <text x="830" y="353">-20</text>
    <text x="852" y="314">-10</text>
    <text x="895" y="301">0</text>
    <text x="933" y="330">10</text>
    <text x="933" y="387">20</text>
  </g>
  <polygon points="926.4,341.6 954,334.8 928.4,347.4" fill="var(--gold)"/>
  <circle cx="885" cy="360" r="42" fill="#0d0d0d" stroke="#5a5a5a" stroke-width="3"/>
  <g font-family="Barlow Semi Condensed, sans-serif" text-anchor="middle">
    <text x="885" y="344" font-size="6.6" font-weight="600" fill="#9fc7e8">EPS</text>
    <text x="885" y="351" font-size="6.6" font-weight="600" fill="#9fc7e8">GROWTH</text>
    <text x="886" y="371" font-size="18" font-weight="700" fill="#f4f4f4">11.9%</text>
  </g>

  <!-- main body with flange -->
  <path d="M155,420 L1038,420 Q1050,420 1050,434 Q1050,450 1030,450 L960,450 Q932,450 932,478 L932,1040 Q932,1066 906,1066 L287,1066 Q261,1066 261,1040 L261,478 Q261,450 233,450 L163,450 Q143,450 143,434 Q143,420 155,420 Z" fill="var(--shell)" stroke="var(--shell-edge)" stroke-width="3"/>
  <path d="M271,470 L271,1036 Q271,1056 291,1056 L902,1056 Q922,1056 922,1036 L922,470" fill="none" stroke="#3c3c3c" stroke-width="2"/>

  <!-- title band -->
  <path d="M372,356 L834,356 L905,398 L288,398 Z" fill="#0c0c0c" stroke="#4c4c4c" stroke-width="2"/>
  <path d="M288,398 L905,398" stroke="#888" stroke-width="1.5"/>
</svg>

<div class="title"><em>OPEN COMPASS</em><sup>TM</sup> SPEEDOMETER</div>

<span class="status-head" style="left:402px">GEAR</span>
<span class="status-head" style="left:609px">CURRENT TREND</span>
<span class="status-head" style="left:801px">LAST TREND CHANGE</span>

<div class="status-row row-bull"><div class="c-gear">2&nbsp; TURBO BOOST</div><div class="c-trend">BULL</div><div class="c-date">FRIDAY, AUGUST 15, 2025</div></div>
<div class="status-row row-bullish"><div class="c-gear">1&nbsp; ACCELERATOR PEDAL</div><div class="c-trend">BULLISH</div><div class="c-date">-</div></div>
<div class="status-row row-bearish"><div class="c-gear">0&nbsp; BRAKES</div><div class="c-trend">BEARISH</div><div class="c-date">-</div></div>
<div class="status-row row-bear"><div class="c-gear">-1&nbsp; REVERSE</div><div class="c-trend">BEAR</div><div class="c-date">-</div></div>

<div class="summary-head">
  <span class="left" style="left:7px">GEAR</span>
  <span class="left" style="left:52px">TREND SUMMARY</span>
  <span style="left:200px">TOTAL DAYS</span>
  <span style="left:292px">PERCENT<br>TOTAL DAYS</span>
  <span style="left:384px">$1000,000<br>INVESTED</span>
  <span style="left:477px">LC500*<br>ANNUALIZED<br>RETURN GAIN (LOSS)</span>
  <span style="left:564px">MAX<br>DROPDOWN</span>
</div>

<div class="summary-row s-turbo"><span class="name">2&nbsp; TURBO BOOST</span><span style="left:198px">3564</span><span style="left:286px">69.11%</span><span style="left:384px">$729,158</span><span style="left:481px">15.08%</span><span style="left:566px">15.08%</span></div>
<div class="summary-row s-accel"><span class="name">1&nbsp; ACCELERATOR PEDAL</span><span style="left:198px">527</span><span style="left:286px">10.22%</span><span style="left:384px">$249,993</span><span style="left:481px">54.98%</span><span style="left:566px">54.98%</span></div>
<div class="summary-row s-brakes"><span class="name">0&nbsp; BRAKES</span><span style="left:198px">937</span><span style="left:286px">18.17%</span><span style="left:384px">$82,111</span><span style="left:481px">-5.16%</span><span style="left:566px">-5.16%</span></div>
<div class="summary-row s-reverse"><span class="name">-1&nbsp; REVERSE</span><span style="left:198px">129</span><span style="left:286px">2.50%</span><span style="left:384px">$55,334</span><span style="left:481px">-68.53%</span><span style="left:566px">-68.53%</span></div>

<div class="total-row"><span class="total-label">TOTAL</span><span class="total-days">5157</span><span class="total-note">LC500 (LCX)*ANNUAL RETURN &amp; DRAWDOWN</span></div>

<div class="rule" style="top:800px"></div>
<div class="logic-title">TREND LOGIC - REQUIRED FOR GEAR SELECTION</div>

<div class="cell h tg" style="left:295px;top:848px;width:141px">TURBO BOOST (BULL)</div>
<div class="cell h tl" style="left:439px;top:848px;width:151px">ACCELERATOR (BULLISH)</div>
<div class="cell h ty" style="left:593px;top:848px;width:151px">BRAKES (BEARISH)</div>
<div class="cell h tr" style="left:747px;top:848px;width:147px">REVERSE (BEAR)</div>

<div class="cell l tg" style="left:295px;top:877px;width:71px">DELTA-V=</div>
<div class="cell v pos" style="left:369px;top:877px;width:67px">POSITIVE</div>
<div class="cell l tg" style="left:295px;top:908px;width:71px">DELTA-V=</div>
<div class="cell v pos" style="left:369px;top:908px;width:67px">POSITIVE</div>

<div class="cell l tl" style="left:439px;top:877px;width:81px">CALENDAR =</div>
<div class="cell v pos" style="left:523px;top:877px;width:67px">POSITIVE</div>
<div class="cell l tl" style="left:439px;top:908px;width:81px">TURBO =</div>
<div class="cell v neg" style="left:523px;top:908px;width:67px">NEGATIVE</div>

<div class="cell l ty" style="left:593px;top:877px;width:81px">CALENDAR =</div>
<div class="cell v neg" style="left:677px;top:877px;width:67px">NEGATIVE</div>
<div class="cell l ty" style="left:593px;top:908px;width:81px">TURBO =</div>
<div class="cell v neg" style="left:677px;top:908px;width:67px">NEGATIVE</div>
<div class="cell l ty" style="left:593px;top:939px;width:81px">REVERSE =</div>
<div class="cell v neg" style="left:677px;top:939px;width:67px">NEGATIVE</div>

<div class="cell l tr" style="left:747px;top:877px;width:87px;justify-content:center">CALENDAR<br>AND TURBO =</div>
<div class="cell v neg" style="left:837px;top:877px;width:57px">NEGATIVE</div>
<div class="cell l tr" style="left:747px;top:908px;width:87px;justify-content:center">STARFLUX<br>L/S =</div>
<div class="cell v neg" style="left:837px;top:908px;width:57px">NEGATIVE</div>
<div class="cell l tr" style="left:747px;top:939px;width:87px;justify-content:center">GOLD<br>ASTROTREND =</div>
<div class="cell v neg" style="left:837px;top:939px;width:57px">NEGATIVE</div>

<div class="rule" style="top:980px"></div>

<p class="disclaimer">*The LC500 is an unmanaged market capitalization weighted index of 500 common stocks chosen for market size, liquidity, and industry group representation to denote U.S. equity performance. LCX is an ETF that is managed to track the LC500 index and is used for this comparison. CAGR a Compound Annual Growth Rate. **Maximum Drawdown is the maximum loss from a peak to a trough of a portfolio, before a new peak is attained. Past performance is no guarantee of future results.</p>

</body>
</html>
```